New Zealand Marlborough Sauvignon Blanc wine packaging design

We need packaging design for our new wine brand, Dunmore Vale. The wine is a New Zealand Marlborough Sauvignon Blanc. We would like the packaging will portray elegance and style with an understated label. We are looking for a label that portrays the elegance of the French Riviera. The label should be round or pill shaped.
Updates

Industry/Entity Type

Wine

Font styles to use
Serif
Sans Serif

Requirements
Must have
• The words in order of importance: Dunmore Vale, Sauvignon Blanc, Marlborough, New Zealand. It should be fit to the bottle posted in the links
Nice to have
• a pill shape or circular shape
Should not have
• Illustrations of wine bottles, wine glasses, or grapes

```html
<!DOCTYPE html>
<html lang="en">
<head>
<meta charset="utf-8">
<title>Dunmore Vale – Marlborough Sauvignon Blanc Label</title>
<link rel="stylesheet" href="https://fonts.googleapis.com/css2?family=Alfa+Slab+One&family=Cabin+Condensed:wght@600&family=Playfair+Display:wght@500&family=Bodoni+Moda:wght@400&display=swap">
<style>
  :root {
    --backdrop: #f8941f;
    --label-cream: #fdf5ec;
    --ink: #111111;
    --art-light: #f6eee3;
    --art-dark: #1a1a1a;
    --art-mid: #4a4744;
  }
  html, body {
    margin: 0;
    padding: 0;
    width: 846px;
    height: 1200px;
    overflow: hidden;
  }
  body {
    background: var(--backdrop);
    display: flex;
    align-items: center;
    justify-content: center;
  }
  .wine-label {
    width: 680px;
    height: 920px;
    display: block;
    filter: drop-shadow(0 6px 14px rgba(0,0,0,0.25));
  }
  .label-face { fill: var(--label-cream); }
  .label-border { fill: none; stroke: var(--ink); stroke-width: 3; }
  .estate-scene { fill: url(#sceneTone); }
  .name-band { fill: var(--ink); }
  .wine-type {
    font-family: "Playfair Display", serif;
    font-weight: 500;
    fill: var(--ink);
    text-anchor: middle;
  }
  .brand-name {
    font-family: "Alfa Slab One", serif;
    font-size: 60px;
    fill: var(--label-cream);
    text-anchor: middle;
  }
  .varietal {
    font-family: "Cabin Condensed", sans-serif;
    font-weight: 600;
    font-size: 46px;
    fill: var(--ink);
    text-anchor: middle;
  }
  .rule { stroke: var(--ink); stroke-width: 1.6; }
  .volume-line {
    font-family: "Bodoni Moda", serif;
    font-size: 28px;
    fill: var(--ink);
    text-anchor: middle;
    letter-spacing: 8px;
    font-variant-numeric: lining-nums;
  }
  .dot, .star { fill: var(--ink); }
</style>
</head>
<body>
<svg class="wine-label" viewBox="0 0 680 920" xmlns="http://www.w3.org/2000/svg">
  <defs>
    <clipPath id="innerOval">
      <ellipse cx="340" cy="460" rx="317" ry="437"/>
    </clipPath>
    <radialGradient id="sceneTone" cx="0.5" cy="1" r="0.75" gradientTransform="translate(0.5 1) scale(1 1.3) translate(-0.5 -1)">
      <stop offset="0" stop-color="var(--art-light)"/>
      <stop offset="0.22" stop-color="var(--art-light)"/>
      <stop offset="0.4" stop-color="var(--art-mid)"/>
      <stop offset="0.6" stop-color="var(--art-dark)"/>
      <stop offset="0.85" stop-color="var(--art-mid)"/>
      <stop offset="1" stop-color="var(--art-light)"/>
    </radialGradient>
  </defs>

  <ellipse class="label-face" cx="340" cy="460" rx="338" ry="458"/>

  <g clip-path="url(#innerOval)">
    <rect class="estate-scene" x="0" y="116" width="680" height="276" role="img"
          aria-label="Black ink engraving of a grand Riviera estate with towers and a tree-lined drive"/>
    <text class="wine-type" x="340" y="346" font-size="26" letter-spacing="4">WHITE</text>
    <text class="wine-type" x="340" y="384" font-size="42" letter-spacing="6">WINE</text>
    <rect class="name-band" x="0" y="392" width="680" height="133"/>
    <text class="brand-name" x="340" y="484" textLength="556" lengthAdjust="spacingAndGlyphs">DUNMORE VALE</text>
  </g>

  <ellipse class="label-border" cx="340" cy="460" rx="317" ry="437"/>

  <text class="varietal" x="340" y="585" textLength="545" lengthAdjust="spacingAndGlyphs">New Zealand Marlborough</text>
  <text class="varietal" x="340" y="643" textLength="350" lengthAdjust="spacingAndGlyphs">Sauvignon Blanc</text>

  <line class="rule" x1="142" y1="700" x2="534" y2="700"/>
  <circle class="dot" cx="152" cy="731" r="7"/>
  <text class="volume-line" x="340" y="740">750mL 13%Alc</text>
  <circle class="dot" cx="526" cy="731" r="7"/>
  <line class="rule" x1="142" y1="757" x2="534" y2="757"/>

  <g class="stars">
    <polygon class="star" transform="translate(288 822)" points="0,-14 4.1,-4.3 13.3,-4.3 5.9,1.6 8.2,11.3 0,5.6 -8.2,11.3 -5.9,1.6 -13.3,-4.3 -4.1,-4.3"/>
    <polygon class="star" transform="translate(335 808)" points="0,-14 4.1,-4.3 13.3,-4.3 5.9,1.6 8.2,11.3 0,5.6 -8.2,11.3 -5.9,1.6 -13.3,-4.3 -4.1,-4.3"/>
    <polygon class="star" transform="translate(382 822)" points="0,-14 4.1,-4.3 13.3,-4.3 5.9,1.6 8.2,11.3 0,5.6 -8.2,11.3 -5.9,1.6 -13.3,-4.3 -4.1,-4.3"/>
  </g>
</svg>
</body>
</html>
```